Clear Plastic Card Design

I am looking to have a business card designed from my logo icon. I am looking to match the style of a different business card I have attached in the files.
Looking for a card that is plastic, with layers of transparency in the shape of my logo icon (also attached in the files) - not a circle like the other card. The winning design will incorporate the red icon logo on the front and back and include the charity's name, "Light for the Weary Souls" in the same or similar font, as well as an email and phone number. For now, use the email: email@lightfortheweary-mail.org and the phone number 555-382-7194.
We like how the sample business card has transparency, partial and full opacity layers and a matching color scheme. Files will need to be in vector so that our business card printing company can work with it.
UPDATE:
We've some excellent designs in, thank you everyone! I got an early review from the owner, and he requested a minor redirect to find his perfect design. He wants the design to stand out by NOT being a rectangle. Try instead a circle, square, or best yet - something that falls in the outline of the logo icon, either fully or partially. Thank you, everyone!
Light for the Weary Souls text should be incorporated as well as a phone and email.

```html
<!DOCTYPE html>
<html lang="en">
<head>
<meta charset="utf-8">
<title>Light for the Weary Souls – Clear Business Card</title>
<link rel="stylesheet" href="https://fonts.googleapis.com/css2?family=Arimo:wght@400;700&family=Lexend:wght@300&display=swap">
<style>
  :root {
    --page-bg: #d9d3ce;
    --page-bg-deep: #c9c1ba;
    --clear-base: rgba(255, 255, 255, 0.22);
    --frost-light: rgba(255, 255, 255, 0.58);
    --frost-heavy: rgba(255, 255, 255, 0.78);
    --frost-smoke: rgba(120, 118, 116, 0.28);
    --card-edge: rgba(160, 154, 150, 0.75);
    --brand-red: #c4161c;
    --ink: #1d1d1d;
    --accent-bar: #1a1a1a;
  }
  * { margin: 0; padding: 0; box-sizing: border-box; }
  html, body {
    width: 1200px; height: 900px; overflow: hidden;
    background: linear-gradient(180deg, var(--page-bg) 0%, var(--page-bg-deep) 100%);
  }
  .card {
    position: absolute; left: 281px; top: 236px;
    width: 671px; height: 385px;
    border: 1px solid var(--card-edge);
    border-radius: 0 76px 0 62px;
    overflow: hidden;
    background: var(--clear-base);
    box-shadow: 0 3px 10px rgba(0, 0, 0, 0.10), inset 0 0 0 1px rgba(255, 255, 255, 0.5);
    font-family: "Arimo", Arial, sans-serif;
    color: var(--ink);
  }
  /* Layer 1: partial frost across the information side */
  .frost-panel {
    position: absolute; inset: 0;
    background: linear-gradient(90deg, rgba(255,255,255,0.30) 0%, var(--frost-heavy) 55%, var(--frost-light) 100%);
  }
  /* Layer 2: smoky translucent zone behind the name mark */
  .smoke-layer {
    position: absolute; left: 0; top: 0; width: 360px; height: 100%;
    background:
      radial-gradient(ellipse 120px 90px at 110px 200px, var(--frost-smoke), transparent 70%),
      radial-gradient(ellipse 90px 70px at 60px 110px, rgba(130,128,126,0.18), transparent 70%),
      radial-gradient(ellipse 110px 80px at 200px 300px, rgba(130,128,126,0.16), transparent 70%);
  }
  /* Layer 3: fully clear window strip */
  .clear-window {
    position: absolute; left: 0; bottom: 0; width: 240px; height: 90px;
    background: linear-gradient(0deg, rgba(255,255,255,0.05), transparent);
  }
  .brand-mark {
    position: absolute; left: 38px; top: 62px;
    width: 300px;
    font-weight: 700; font-size: 60px; line-height: 1.02;
    color: var(--brand-red);
    opacity: 0.9;
    letter-spacing: -1px;
  }
  .org-name {
    position: absolute; left: 373px; top: 70px;
    font-family: "Lexend", "Arimo", sans-serif;
    font-weight: 300; font-size: 36px; line-height: 1.17;
    color: var(--ink);
    letter-spacing: -0.3px;
  }
  .person {
    position: absolute; right: 49px; top: 172px;
    text-align: right;
  }
  .person-name {
    font-weight: 700; font-size: 25px; line-height: 1.1;
    color: var(--brand-red); letter-spacing: 0.3px;
  }
  .person-role { font-size: 16px; margin-top: 4px; }
  .divider {
    position: absolute; right: 50px; top: 238px;
    width: 43px; height: 3px; background: var(--brand-red);
  }
  .contacts {
    position: absolute; right: 49px; top: 254px;
    list-style: none; text-align: right;
    font-size: 15px; line-height: 24px;
  }
  .contacts li { display: flex; justify-content: flex-end; align-items: center; gap: 9px; }
  .contacts svg { width: 13px; height: 13px; fill: var(--brand-red); }
  .edge-bar {
    position: absolute; right: 0; top: 179px;
    width: 14px; height: 140px; background: var(--accent-bar);
  }
</style>
</head>
<body>
  <main class="card">
    <div class="frost-panel"></div>
    <div class="smoke-layer"></div>
    <div class="clear-window"></div>

    <div class="brand-mark">Light<br>for the<br>Weary<br>Souls</div>

    <h1 class="org-name">Light for the<br>Weary Souls</h1>

    <div class="person">
      <div class="person-name">DANIEL REYES</div>
      <div class="person-role">Founder &amp; CEO</div>
    </div>
    <div class="divider"></div>

    <ul class="contacts">
      <li>555-382-7194
        <svg viewBox="0 0 24 24" aria-hidden="true"><path d="M6.6 10.8a15 15 0 0 0 6.6 6.6l2.2-2.2a1 1 0 0 1 1-.25 11.4 11.4 0 0 0 3.6.57 1 1 0 0 1 1 1V20a1 1 0 0 1-1 1A17 17 0 0 1 3 4a1 1 0 0 1 1-1h3.5a1 1 0 0 1 1 1c0 1.25.2 2.45.57 3.57a1 1 0 0 1-.25 1z"/></svg>
      </li>
      <li>email@lightfortheweary-mail.org
        <svg viewBox="0 0 24 24" aria-hidden="true"><path d="M2 5h20l-10 7.5z"/><path d="M2 7v12h20V7l-10 7.5z"/></svg>
      </li>
      <li>lightforthewearysouls.org
        <svg viewBox="0 0 24 24" aria-hidden="true"><circle cx="12" cy="12" r="10"/><path d="M3 12h18M12 2c3 3 3 17 0 20M12 2c-3 3-3 17 0 20" fill="none" stroke="#fff" stroke-width="1.6"/></svg>
      </li>
    </ul>

    <div class="edge-bar"></div>
  </main>
</body>
</html>
```